Brightbay Orthodontics business card design

Need a business card design that reflects our re-branding (orthodontic office - braces) and a new partnership with a pediatric dental office. We would like to include "for adults and children" on the card as well so adults know they are welcome to get their braces here as well. Office design is modern and would like business card to reflect a modern type look. Here's the text we would like to be included on the card:

Darren Wolcott, DDS, MSD
5214 West Linden Avenue, Suite 204
Harlow Springs, NM 76991
555-418-2637
www.brightbayortho.example
info@brightbayortho.example

Can we add the following to the existing designs? Darren Wolcott, DDS, MSD 5214 West Linden Avenue, Suite 204 Harlow Springs, NM 76991 555-418-2637

Does anyone have any more vertical designs available? Thanks!

Dental

```html
<!DOCTYPE html>
<html lang="en">
<head>
<meta charset="utf-8">
<title>Brightbay Orthodontics – Business Card</title>
<link href="https://fonts.googleapis.com/css2?family=Open+Sans:wght@400;600;700&display=swap" rel="stylesheet">
<style>
  :root {
    --stage: #e6e6e4;
    --paper: #ffffff;
    --paper-shade: #f1f1f1;
    --ink: #2b2b2b;
    --ink-soft: #555555;
    --magenta: #e5198a;
    --black: #1c1c1c;
    --yellow: #f4e21c;
    --blue: #1f86c8;
    --green: #7cc242;
    --orange: #f08a1d;
    --icon: #3fa34d;
  }
  * { box-sizing: border-box; margin: 0; padding: 0; }
  html, body { width: 1200px; height: 871px; overflow: hidden; }
  body {
    background: var(--stage);
    font-family: "Open Sans", sans-serif;
    color: var(--ink);
    position: relative;
  }
  .card {
    position: absolute;
    top: 146px;
    width: 330px;
    height: 578px;
    background: linear-gradient(160deg, var(--paper) 0%, var(--paper-shade) 100%);
    box-shadow: 0 10px 30px rgba(0,0,0,0.18);
    overflow: hidden;
  }
  .card--front { left: 215px; }
  .card--back  { left: 655px; }

  /* landscape content frame turned to sit in the portrait card */
  .face {
    position: absolute;
    width: 578px;
    height: 330px;
    left: -124px;
    top: 124px;
  }
  .card--front .face { transform: rotate(90deg); }
  .card--back .face  { transform: rotate(-90deg); }

  /* front */
  .brand-name {
    position: absolute;
    left: 190px;
    top: 70px;
    display: flex;
    align-items: center;
    gap: 14px;
    font-weight: 700;
    font-size: 40px;
    line-height: 1.05;
    color: var(--ink);
  }
  .brand-dot {
    width: 26px; height: 26px; border-radius: 50%;
    background: var(--magenta);
    flex: none;
  }
  .audience-band {
    position: absolute;
    left: 0;
    height: 44px;
    display: flex;
    align-items: center;
    padding-left: 56px;
    color: #fff;
    font-size: 19px;
    letter-spacing: 1px;
    text-transform: uppercase;
  }
  .audience-band--children { top: 238px; width: 300px; background: var(--magenta); }
  .audience-band--adults   { top: 282px; width: 245px; background: var(--black); }

  /* back */
  .brand-name--small {
    left: auto;
    right: 30px;
    top: 26px;
    font-size: 22px;
    gap: 10px;
  }
  .brand-name--small .brand-dot { width: 16px; height: 16px; }
  .color-strip {
    position: absolute;
    left: 0; top: 0;
    width: 24px; height: 100%;
    display: flex;
    flex-direction: column-reverse;
  }
  .color-strip span { flex: 1; }
  .color-strip .yellow { background: var(--yellow); }
  .color-strip .blue   { background: var(--blue); }
  .color-strip .magenta{ background: var(--magenta); }
  .color-strip .green  { background: var(--green); }
  .color-strip .orange { background: var(--orange); }

  .contact {
    position: absolute;
    left: 66px;
    top: 150px;
  }
  .contact__name {
    font-weight: 700;
    font-size: 20px;
    color: var(--ink);
    margin-bottom: 14px;
  }
  .contact__columns { display: flex; gap: 26px; }
  .contact__address {
    font-size: 13px;
    line-height: 1.55;
    color: var(--ink-soft);
  }
  .contact__lines { list-style: none; font-size: 13px; line-height: 1.55; color: var(--ink-soft); }
  .contact__lines li { display: flex; align-items: center; gap: 8px; }
  .contact__lines svg { width: 12px; height: 12px; flex: none; }
</style>
</head>
<body>

  <section class="card card--front" aria-label="Card front">
    <div class="face">
      <div class="brand-name"><span class="brand-dot"></span><span>Brightbay<br>Orthodontics</span></div>
      <div class="audience-band audience-band--children">For children</div>
      <div class="audience-band audience-band--adults">and adults</div>
    </div>
  </section>

  <section class="card card--back" aria-label="Card back">
    <div class="face">
      <div class="color-strip">
        <span class="yellow"></span><span class="blue"></span><span class="magenta"></span><span class="green"></span><span class="orange"></span>
      </div>
      <div class="brand-name brand-name--small"><span class="brand-dot"></span><span>Brightbay Orthodontics</span></div>
      <div class="contact">
        <p class="contact__name">Darren Wolcott, DDS, MSD</p>
        <div class="contact__columns">
          <p class="contact__address">5214 West Linden Avenue, Suite 204<br>Harlow Springs, NM 76991</p>
          <ul class="contact__lines">
            <li>
              <svg viewBox="0 0 12 12"><path d="M3 1h2l1 3-1.5 1a6 6 0 0 0 2.5 2.5L8 6l3 1v2a1.5 1.5 0 0 1-1.5 1.5A8.5 8.5 0 0 1 1.5 2.5 1.5 1.5 0 0 1 3 1z" fill="var(--icon)"/></svg>
              555-418-2637
            </li>
            <li>
              <svg viewBox="0 0 12 12"><rect x="1" y="2.5" width="10" height="7" rx="1" fill="none" stroke="var(--icon)" stroke-width="1.3"/><path d="M1.5 3l4.5 3.5L10.5 3" fill="none" stroke="var(--icon)" stroke-width="1.3"/></svg>
              info@brightbayortho.example
            </li>
            <li>
              <svg viewBox="0 0 12 12"><circle cx="6" cy="6" r="4.8" fill="none" stroke="var(--icon)" stroke-width="1.3"/><path d="M1.2 6h9.6M6 1.2c2.2 2.6 2.2 7 0 9.6M6 1.2c-2.2 2.6-2.2 7 0 9.6" fill="none" stroke="var(--icon)" stroke-width="1"/></svg>
              www.brightbayortho.example
            </li>
          </ul>
        </div>
      </div>
    </div>
  </section>

</body>
</html>
```